Staff Newsletter Template Image

We are looking for two .jpg images that we can put into a Word document and use for our staff newsletter. We will then add content using text boxes.
Attached is the current template which works for the columns and size that we need but we just want a fresh new design.
The Word document shows how we use it.
The name will stay the same - Brightwave Post but can be a different look to the current one.

Target Market(s)

Sales team

Colors

Designer to choose colors to be used in the design.

Requirements
Must have
• Colours will be green, grey and white, possibly cream if needed. All from the guidelines.
• I have attached our brand guidelines which shows design elements and fonts for our brand. Also attached is brand guidelines for one of our product lines as we would like to use the same green.
• It needs to be nice to look at and motivational for our team

```html
<!DOCTYPE html>
<html lang="en">
<head>
<meta charset="utf-8">
<title>Brightwave Post – Staff Newsletter</title>
<link rel="stylesheet" href="https://fonts.googleapis.com/css2?family=Cinzel:wght@500&display=swap">
<style>
  :root {
    --charcoal: #3a3b3b;
    --charcoal-deep: #2c2d2d;
    --leaf-green: #46ad4b;
    --lime-green: #8cc63f;
    --paper: #ffffff;
  }
  html, body {
    margin: 0;
    padding: 0;
    overflow: hidden;
    background: var(--paper);
  }
  .newsletter-page {
    position: relative;
    width: 884px;
    height: 1200px;
    overflow: hidden;
    background: var(--paper);
  }
  .header-swoosh,
  .footer-swoosh {
    position: absolute;
    left: 0;
    display: block;
  }
  .header-swoosh { top: 0; }
  .footer-swoosh { bottom: 0; }
  .swoosh-lime { fill: var(--lime-green); }
  .swoosh-leaf { fill: var(--leaf-green); }
  .swoosh-charcoal { fill: var(--charcoal); }
  .footer-bar { fill: var(--charcoal); }
  .masthead {
    position: absolute;
    top: 62px;
    left: 56px;
    display: flex;
    align-items: center;
    gap: 10px;
    color: var(--paper);
    font-family: "Cinzel", "Times New Roman", serif;
    font-weight: 500;
    font-size: 22px;
    letter-spacing: 0.04em;
  }
  .masthead-dot {
    width: 12px;
    height: 12px;
    border-radius: 50%;
    background: var(--paper);
  }
</style>
</head>
<body>
  <main class="newsletter-page">
    <svg class="header-swoosh" width="884" height="340" viewBox="0 0 884 340" aria-hidden="true">
      <path class="swoosh-lime" d="M0,0 H884 V168 C790,262 610,330 430,330 C250,330 90,280 0,150 Z"/>
      <path class="swoosh-leaf" d="M0,0 H830 C780,140 640,248 430,250 C250,252 80,180 0,100 Z"/>
      <path class="swoosh-charcoal" d="M0,0 H780 C700,150 560,226 380,229 C200,232 70,140 0,60 Z"/>
    </svg>

    <div class="masthead">
      <span class="masthead-dot"></span>
      <span class="masthead-name">Brightwave Post</span>
    </div>

    <svg class="footer-swoosh" width="884" height="200" viewBox="0 1000 884 200" aria-hidden="true">
      <defs>
        <linearGradient id="footer-shade" x1="0" y1="0" x2="1" y2="1">
          <stop offset="0" stop-color="#555656"/>
          <stop offset="1" stop-color="#2c2d2d"/>
        </linearGradient>
      </defs>
      <rect class="footer-bar" x="0" y="1108" width="884" height="92"/>
      <path class="swoosh-lime" d="M656,1200 C686,1096 776,1018 884,1002 V1200 Z"/>
      <path class="swoosh-leaf" d="M682,1200 C712,1118 792,1060 884,1052 V1200 Z"/>
      <path fill="url(#footer-shade)" d="M706,1200 C738,1138 806,1092 884,1084 V1200 Z"/>
    </svg>
  </main>
</body>
</html>
```